Flyers

Modify Existing Flyer and create another for exterior company
Updates

Previous Brief has been updated- we want to update this existing one also

Target Market(s)

Exterior Remodeling Customers

Industry/Entity Type

Remodeling/Construction

```html
<!DOCTYPE html>
<html lang="en">
<head>
<meta charset="utf-8">
<title>Ridgeline Roofing and Exteriors Flyer</title>
<link href="https://fonts.googleapis.com/css2?family=Exo+2:ital,wght@0,400;0,500;0,700;1,400;1,800;1,900&family=Roboto:wght@500;700&display=swap" rel="stylesheet">
<style>
  :root {
    --navy: #0b0f17;
    --blue: #0a6fcc;
    --blue-bright: #1380e0;
    --orange: #ee5a24;
    --ink: #1d1d1f;
    --pale-blue: #d3e0f0;
    --white: #ffffff;
  }
  * { margin: 0; padding: 0; box-sizing: border-box; }
  html, body { width: 960px; height: 1200px; overflow: hidden; background: var(--white); }
  .flyer { position: relative; width: 960px; height: 1200px; overflow: hidden; background: var(--white); font-family: "Exo 2", sans-serif; color: var(--ink); }

  .hero-photo {
    position: absolute; left: 0; top: 0; width: 960px; height: 528px;
    background: linear-gradient(180deg, #07090e 0%, #141c2a 28%, #4a5a72 52%, #8c9ab0 72%, #cfd6e0 88%, #ffffff 100%);
  }
  .brand-box {
    position: absolute; left: 37px; top: 51px; width: 308px; height: 120px;
    background: #000; display: flex; align-items: center; justify-content: center; gap: 10px;
  }
  .brand-box .mark { width: 14px; height: 14px; background: var(--orange); }
  .brand-name { font-family: "Exo 2", sans-serif; font-weight: 700; font-size: 21px; color: var(--white); letter-spacing: 0.3px; line-height: 1.2; text-align: left; }

  .headline { position: absolute; left: 520px; top: 36px; width: 380px; text-align: center; font-weight: 900; font-style: italic; font-size: 33px; line-height: 37px; letter-spacing: -0.5px; text-transform: uppercase; }
  .headline .blue { color: var(--blue-bright); display: block; }
  .headline .orange { color: var(--orange); display: block; }

  .house-photo {
    position: absolute; left: 54px; top: 528px; width: 363px; height: 251px;
    border: 1px solid #333;
    background: linear-gradient(180deg, #9bb3d8 0%, #c4cfe4 38%, #8c8676 55%, #6f8a4d 78%, #4f8a2e 100%);
  }
  .section-tab { position: absolute; left: 438px; top: 528px; height: 41px; }
  .section-tab svg { position: absolute; left: 0; top: 0; }
  .section-tab h2 { position: relative; font-family: "Roboto", sans-serif; font-weight: 700; font-size: 25px; color: var(--white); line-height: 41px; padding-left: 10px; letter-spacing: 0.2px; }
  .subhead { position: absolute; left: 438px; top: 572px; font-style: italic; font-size: 23px; color: var(--orange); }
  .body-copy { position: absolute; left: 442px; top: 610px; width: 463px; font-size: 14px; line-height: 18.5px; text-align: justify; hyphens: auto; }
  .body-copy p + p { margin-top: 8px; }

  .service-band { position: absolute; left: 0; top: 835px; width: 960px; height: 68px; background: var(--orange); display: flex; align-items: center; justify-content: center; gap: 14px; }
  .band-notch { position: absolute; left: 760px; top: 825px; }
  .service { display: flex; align-items: center; gap: 8px; font-family: "Roboto", sans-serif; font-weight: 700; font-size: 23px; color: var(--white); }
  .service svg { flex: none; }

  .quote-mark { position: absolute; font-family: "Roboto", sans-serif; font-weight: 700; color: var(--pale-blue); font-size: 300px; line-height: 1; }
  .quote-open { left: -14px; top: 884px; }
  .quote-close { left: 296px; top: 1088px; }
  .reviews { position: absolute; left: 110px; top: 944px; width: 310px; text-align: center; }
  .reviews h3 { font-family: "Roboto", sans-serif; font-weight: 700; font-size: 24px; color: var(--blue); margin-bottom: 12px; }
  .reviews p { font-size: 14px; line-height: 19px; }
  .reviews .reviewer { color: var(--orange); font-weight: 500; margin-top: 20px; font-size: 14px; }

  .cta-shape { position: absolute; left: 0; top: 0; }
  .cta { position: absolute; left: 574px; top: 938px; width: 380px; text-align: center; color: var(--white); }
  .cta h3 { font-family: "Roboto", sans-serif; font-weight: 500; font-size: 19.5px; line-height: 25px; }
  .cta .lead { font-style: italic; font-size: 15.5px; line-height: 20px; margin-top: 4px; }
  .cta .phone { font-weight: 700; font-size: 41px; line-height: 44px; margin-top: 14px; letter-spacing: 0.5px; }
  .cta .web { font-weight: 500; font-size: 25px; line-height: 28px; }
  .cta .address { font-size: 14.5px; line-height: 19px; margin-top: 14px; }
</style>
</head>
<body>
<main class="flyer">
  <div class="hero-photo" role="img" aria-label="Photo of a grey shingle roof with brick chimneys and a roofer crouching on the ridge against a dark sky"></div>

  <div class="brand-box">
    <span class="mark"></span>
    <span class="brand-name">RIDGELINE<br>ROOFING AND EXTERIORS</span>
  </div>

  <h1 class="headline">
    <span class="blue">Boost your</span>
    <span class="blue">property value</span>
    <span class="orange">with a brand</span>
    <span class="orange">new roof</span>
  </h1>

  <div class="house-photo" role="img" aria-label="Photo of a two-storey home with grey siding, stone base and green lawn"></div>

  <div class="section-tab">
    <svg width="440" height="41" viewBox="0 0 440 41"><polygon points="0,0 430,0 440,41 0,41" fill="var(--blue)"/></svg>
    <h2>TRANSFORM YOUR EXTERIOR</h2>
  </div>
  <p class="subhead">We install new decks, siding &amp; roofs</p>

  <div class="body-copy">
    <p>If you want to increase your property value, updating your exterior is a great option. The team at Ridgeline Roofing &amp; Exteriors has over 25 years of experience installing and repairing roofs, so you can count on us to do an amazing job.</p>
    <p>Along with being experienced roofers, we're also extremely skilled deck and siding installers. You can add an exciting outdoor entertainment area to your property with a brand-new deck from us. Depend on us to take on your exterior improvement job in the Ankeny, IA area.</p>
  </div>

  <svg class="band-notch" width="24" height="12" viewBox="0 0 24 12"><polygon points="0,12 12,0 24,12" fill="var(--blue)"/></svg>
  <div class="service-band">
    <div class="service">
      <svg width="40" height="38" viewBox="0 0 40 38" fill="none" stroke="#fff" stroke-width="1.6"><path d="M3 18 20 3 37 18"/><path d="M8 14v22h24V14"/><rect x="14" y="20" width="12" height="10"/><path d="M20 20v10M14 25h12M4 36h32"/></svg>
      SIDING
    </div>
    <div class="service">
      <svg width="32" height="36" viewBox="0 0 32 36" fill="none" stroke="#fff" stroke-width="1.6"><rect x="2" y="2" width="28" height="32"/><path d="M9 2v32M16 2v32M23 2v32"/></svg>
      DECKING
    </div>
    <div class="service">
      <svg width="46" height="32" viewBox="0 0 46 32" fill="none" stroke="#fff" stroke-width="1.6"><path d="M10 3h26l8 26H2z"/><path d="M4 22h38M7 14h32M16 3l-4 26M23 3v26M30 3l4 26"/></svg>
      METAL ROOFING
    </div>
    <div class="service">
      <svg width="40" height="38" viewBox="0 0 40 38" fill="none" stroke="#fff" stroke-width="1.6"><path d="M3 18 20 3 37 18"/><path d="M8 14v22h24V14"/><path d="M20 3l-3 8 5 4-4 7"/><rect x="16" y="26" width="8" height="10"/></svg>
      STORM DAMAGE
    </div>
  </div>

  <span class="quote-mark quote-open">&ldquo;</span>
  <span class="quote-mark quote-close">&rdquo;</span>

  <section class="reviews">
    <h3>CUSTOMER REVIEWS</h3>
    <p>What a beautiful kitchen! We hired Ridgeline Exteriors - they truly are a wonderful company to work with. From our first meeting until the last day we enjoyed all the workers in our home. Great local company!</p>
    <p class="reviewer">Marla T.</p>
  </section>

  <svg class="cta-shape" width="960" height="1200" viewBox="0 0 960 1200"><polygon points="353,1200 705,904 861,904 960,990 960,1200" fill="var(--blue)"/></svg>

  <section class="cta">
    <h3>NEED ROOF<br>REPAIR SERVICES?</h3>
    <p class="lead">Contact a local roofing company<br>serving the Des Moines area</p>
    <p class="phone">(555) 014-2290</p>
    <p class="web">RIDGELINEHOMEPROS.COM</p>
    <p class="address">48 Harbor Mill Road<br>Suite 210, Ankeny, IA 50021</p>
  </section>
</main>
</body>
</html>
```